Harvest Gateway Fellowship Ministries needs a fresh new web design

We are an up and coming multicultural church that aims to bring people into a life changing encounter with God. We need a fresh and inviting website in order to increase our internet presence and make us easier to connect with.
Here are some of the basic requirements for the site:
• Clearly displayed address, service times, and contact info
• A staff profile page
• An area for a calendar with upcoming events and their details
• Social media buttons
• Group pages for the different ministries (youth, children’s church, men, etc…)
• An area for donations and eCommerce
• A resources page for assorted media (podcasts, sermons, videos, etc.…)
• An area for prayer requests.

```html
<!DOCTYPE html>
<html lang="en">
<head>
<meta charset="utf-8">
<title>Harvest Gateway Fellowship Ministries</title>
<link rel="stylesheet" href="https://fonts.googleapis.com/css2?family=Ubuntu:wght@400;500&family=Ubuntu+Condensed&family=Open+Sans:wght@400;600&family=Arimo&display=swap">
<style>
:root{
  --blue:#0d5c8a;
  --navy:#154f78;
  --teal:#1a8fb5;
  --gold:#e8b52a;
  --grey:#eeeeee;
  --text:#333;
  --dark:#2b2b2b;
  --darker:#222;
  --footer-text:#c9c9c9;
}
*{margin:0;padding:0;box-sizing:border-box}
html,body{width:1051px;height:1200px;overflow:hidden;background:#fff}
body{font-family:'Open Sans',sans-serif;color:var(--text);position:relative}
.abs{position:absolute}
.topline{left:0;top:0;width:1051px;height:3px;background:var(--blue)}
.brand{left:119px;top:20px;width:140px;text-align:center}
.brand-mark{width:48px;height:48px;border-radius:50%;background:var(--gold);margin:0 auto 8px}
.brand-name{font-family:'Ubuntu',sans-serif;font-size:11px;color:var(--navy);line-height:14px}
.callus{left:743px;top:43px;font-family:'Ubuntu',sans-serif;font-size:14px;color:#444;display:flex;align-items:center;gap:6px}
.callus strong{font-weight:500}
.callus .num{font-size:18px;color:#555}
.search{left:745px;top:85px;width:181px;height:21px;border:1px solid #ccc;border-radius:5px;background:#f7f7f7;font-size:9px;color:#999;padding:4px 10px;font-style:italic}
.search svg{position:absolute;right:7px;top:4px}
.nav{left:123px;top:148px;width:805px;height:34px;background:var(--gold);border:3px solid #f2f2f2;box-shadow:0 0 3px #bbb;display:flex;justify-content:space-between;align-items:center;padding:0 12px}
.nav a{font-family:'Ubuntu',sans-serif;font-size:12px;color:var(--blue);text-decoration:none}
.hero{left:123px;top:189px;width:805px;height:341px;border:1px solid #ddd;background:#fff;box-shadow:0 6px 8px -6px #999}
.hero-photo{left:128px;top:194px;width:551px;height:331px;background:linear-gradient(160deg,#d9d2c4,#8a7a6a 45%,#3c3430)}
.dots{left:456px;top:499px;width:139px;height:26px}
.prayer{left:679px;top:194px;width:245px;height:331px;background:var(--teal)}
.prayer h2{font-family:'Ubuntu',sans-serif;font-weight:400;color:#fff;font-size:16px;text-align:center;margin-top:15px}
.prayer-box{left:696px;top:245px;width:213px;height:247px;background:#fff;padding:11px 12px;font-size:9.5px;line-height:18px}
.field{display:flex;align-items:center;margin-top:6px;font-size:8.5px}
.field span{width:45px}
.field i{display:block;width:138px;height:16px;background:#ececec;border:1px solid #ddd}
.check{font-size:7.5px;margin:6px 0 0 16px;display:flex;align-items:center;gap:5px}
.check i{width:7px;height:7px;border:1px solid #bbb;display:block}
.submit{display:block;margin:12px auto 0;width:122px;height:25px;background:var(--navy);color:#fff;font-family:'Ubuntu',sans-serif;font-size:13px;text-align:center;line-height:25px}
.social-login{display:flex;margin:8px auto 0;width:102px;height:20px;background:#3b5a98;color:#fff;font-size:7px;align-items:center;border-radius:2px}
.social-login b{width:17px;height:20px;background:#2e4a82;display:block;margin-right:6px;border-radius:2px 0 0 2px}
.welcome{left:123px;top:550px;width:805px;text-align:center}
.welcome h1{font-family:'Arimo',sans-serif;font-weight:400;font-size:18px;color:var(--blue)}
.welcome h1 b{font-weight:400;margin-left:8px;color:var(--navy)}
.welcome p{font-size:10.5px;line-height:20px;margin-top:6px}
.col-h{font-family:'Ubuntu',sans-serif;font-weight:400;font-size:16px;color:var(--blue)}
.video{left:123px;top:694px;width:246px;height:203px;background:#000}
.video-img{position:absolute;left:0;top:12px;width:246px;height:164px;background:linear-gradient(135deg,#2f5a9c,#5f7a52 40%,#2a4f8c)}
.video-bar{position:absolute;left:0;bottom:6px;width:246px;height:20px;background:#333;display:flex;align-items:center;padding:0 6px;gap:6px}
.video-bar i{flex:1;height:12px;background:linear-gradient(#eee,#bbb);display:block}
.cal{left:420px;top:694px;width:211px;box-shadow:0 2px 4px #999}
.cal-head{height:34px;background:#444;color:#fff;font-family:'Arimo',sans-serif;font-size:14px;display:flex;justify-content:space-between;align-items:center;padding:0 10px}
.cal-days,.cal-grid{display:grid;grid-template-columns:repeat(7,1fr)}
.cal-days{height:20px;background:#f4f4f4;font-size:7px;color:#555;align-items:center;text-align:center}
.cal-grid div{height:30px;background:#e6e6e6;border-right:1px solid #fff;border-bottom:1px solid #d2d2d2;display:flex;align-items:center;justify-content:center;font-family:'Arimo',sans-serif;font-size:12px;color:#555}
.cal-grid .muted{color:#bbb;background:#eee}
.cal-grid .today{background:#5fb3cc;color:#2c6f85}
.staff-photo{left:702px;top:695px;width:223px;height:93px;border:1px solid #ccc;padding:3px;background:#fff}
.staff-photo div{width:100%;height:100%;background:linear-gradient(90deg,#bfb6ad,#e26d3c 45%,#7a6a60 75%,#d66c9a)}
.staff-text{left:702px;top:803px;width:225px;font-family:'Arimo',sans-serif;font-size:9.5px;line-height:18px;color:#222}
.staff-list{left:702px;top:861px;width:225px;display:grid;grid-template-columns:1fr 1fr;row-gap:8px;font-family:'Arimo',sans-serif;font-size:9.5px;color:#222;list-style:none}
.staff-list li::before{content:"→";font-size:7px;margin:0 6px 0 0;color:#666}
.rule{left:123px;top:928px;width:790px;height:1px;background:#ddd}
.footer{left:0;top:951px;width:1051px;height:198px;background:var(--dark);font-family:'Ubuntu Condensed',sans-serif;color:var(--footer-text)}
.footer h3{font-weight:400;font-size:16px;color:#9a9a9a}
.fcol{position:absolute;top:21px}
.fcol ul{list-style:none;font-size:10.5px;line-height:23px;margin-top:7px}
.divider{position:absolute;top:24px;width:1px;height:158px;background:#444}
.quote{font-size:10px;line-height:20.5px;margin-top:8px}
.cards{display:flex;gap:10px;margin-top:8px;align-items:center}
.cards span{width:35px;height:22px;background:#f2f2f2;border-radius:2px;color:#555;font-family:'Ubuntu',sans-serif;font-size:6.5px;display:flex;align-items:center;justify-content:center}
.cards i{width:30px;height:30px;border-radius:50%;background:var(--gold);display:block}
.times{display:grid;grid-template-columns:72px auto;font-size:10.5px;line-height:22px;margin-top:5px}
.connect li{display:flex;align-items:center;gap:12px;line-height:30px}
.connect li::before{content:"";width:25px;height:25px;border-radius:50%;background:#eee;display:block}
.bottom{left:0;top:1149px;width:1051px;height:51px;background:var(--darker);font-family:'Ubuntu Condensed',sans-serif;color:#888;font-size:10.5px;padding:24px 0 0 126px}
</style>
</head>
<body>
<div class="abs topline"></div>

<div class="abs brand">
  <div class="brand-mark"></div>
  <div class="brand-name">Harvest Gateway Fellowship Ministries</div>
</div>

<div class="abs callus">
  <svg width="16" height="12" viewBox="0 0 16 12"><path d="M1 4c0-3 14-3 14 0v1h-4V3.5H5V5H1z M3 6h10l1 6H2z" fill="#444"/></svg>
  <strong>Call Us:</strong><span class="num">555.014.7720</span>
</div>
<div class="abs search">Search...
  <svg width="14" height="12" viewBox="0 0 14 12"><circle cx="5" cy="5" r="3.5" fill="none" stroke="#333" stroke-width="1.6"/><path d="M8 7.5l5 4" stroke="#333" stroke-width="2"/></svg>
</div>

<nav class="abs nav">
  <a href="#">HOME</a><a href="#">ABOUT US</a><a href="#">SERVICES</a><a href="#">DONATION</a><a href="#">EVENT</a><a href="#">CONTACT US</a>
</nav>

<div class="abs hero"></div>
<div class="abs hero-photo" role="img" aria-label="Photo of the congregation worshipping together in the church hall"></div>
<svg class="abs dots" viewBox="0 0 139 26">
  <path d="M12 0h115l12 26H0z" fill="var(--gold)"/>
  <circle cx="37" cy="13" r="6" fill="#222"/>
  <circle cx="59" cy="13" r="6" fill="#7a6222"/>
  <circle cx="81" cy="13" r="6" fill="#7a6222"/>
  <circle cx="103" cy="13" r="6" fill="#7a6222"/>
</svg>

<section class="abs prayer"><h2>PRAYER REQUEST</h2></section>
<div class="abs prayer-box">
  <p>You are invited to submit your prayer requests below. Your requests will be forwarded to the church. If you wish to send your request</p>
  <div class="field" style="margin-top:8px"><span>Name:</span><i></i></div>
  <div class="field"><span>Email:</span><i></i></div>
  <div class="check"><i></i>Update me on free coupons and savings.</div>
  <span class="submit">SUBMIT</span>
  <span class="social-login"><b></b>Login with FriendBook</span>
</div>

<section class="abs welcome">
  <h1>Welcome To <b>Harvest GFM</b></h1>
  <p>Welcome to Harvest Gateway Fellowship Ministries, a place where we can come together and fellowship. HGFM is located in Maple Heights, Ohio and we would love to have you worship with us. We believe God is doing something extraordinary through our church and would like for you to be a part. Please prayerfully consider our church as a place you would like to worship and fellowship with us as we continue to grow.</p>
</section>

<h2 class="abs col-h" style="left:123px;top:655px">Our Featured Videos</h2>
<h2 class="abs col-h" style="left:420px;top:655px">Upcoming event</h2>
<h2 class="abs col-h" style="left:701px;top:660px">Staff Profile</h2>

<div class="abs video">
  <div class="video-img" role="img" aria-label="Featured video still showing a world map"></div>
  <div class="video-bar">
    <svg width="10" height="10" viewBox="0 0 10 10"><path d="M1 0l8 5-8 5z" fill="#999"/></svg>
    <i></i>
    <svg width="12" height="10" viewBox="0 0 12 10"><path d="M0 3h3l4-3v10L3 7H0z" fill="#ccc"/></svg>
  </div>
</div>

<div class="abs cal">
  <div class="cal-head"><span style="font-size:9px">◄</span><span>June 2014</span><span style="font-size:9px">►</span></div>
  <div class="cal-days"><span>MON</span><span>TUE</span><span>WED</span><span>THU</span><span>FRI</span><span>SAT</span><span>SUN</span></div>
  <div class="cal-grid">
    <div class="muted">28</div><div>1</div><div>2</div><div>3</div><div class="today">4</div><div>5</div><div>6</div>
    <div>7</div><div>8</div><div>9</div><div>10</div><div>11</div><div>12</div><div>13</div>
    <div>14</div><div>15</div><div>16</div><div>17</div><div>18</div><div>19</div><div>20</div>
    <div>21</div><div>22</div><div>23</div><div>24</div><div>25</div><div>26</div><div>27</div>
    <div>28</div><div>29</div><div>30</div><div>31</div><div class="muted">1</div><div class="muted">2</div><div class="muted">3</div>
  </div>
</div>

<div class="abs staff-photo"><div role="img" aria-label="Group photo of the ministry staff team"></div></div>
<p class="abs staff-text">Sed ut perspiciatis unde omnis iste natus error sit voluptatem accusantium doloremque laudantium, totam rem aperiam</p>
<ul class="abs staff-list"><li>Laboris</li><li>Voluptate Series</li><li>Commodo</li><li>Voluptate Series</li></ul>

<div class="abs rule"></div>

<footer class="abs footer">
  <div class="fcol" style="left:123px">
    <h3>COMPANY</h3>
    <ul><li>COMPANY OVERVIEW</li><li>ABOUT US</li><li>SERVICES PROVIDE</li><li>OUR PROCESS</li><li>OUR CLIENTS</li></ul>
  </div>
  <div class="divider" style="left:250px"></div>
  <div class="fcol" style="left:283px;width:270px">
    <h3>DONATIONS</h3>
    <p class="quote">MATTHEW 25: 40<br>"THE KING WILL REPLY, 'TRULY I TELL YOU, WHATEVER YOU DID FOR ONE OF THE LEAST OF THESE BROTHERS AND SISTERS OF MINE, YOU DID FOR ME.</p>
    <div class="cards"><span>PayWell</span><span>Vexa</span><span>CardOne</span><span>Dyscor</span><span>AmeriPay</span><i></i></div>
  </div>
  <div class="divider" style="left:572px"></div>
  <div class="fcol" style="left:607px;top:19px">
    <h3>SERVICES TIMINGS</h3>
    <div class="times"><span>Monday :</span><span>10 am - 12pm</span><span>Tuesday :</span><span>10 am - 12pm</span><span>Wednesday :</span><span>10 am - 12pm</span><span>Thursday :</span><span>10 am - 12pm</span><span>Friday:</span><span>10 am - 12pm</span><span>Saturday :</span><span>10 am - 12pm</span></div>
  </div>
  <div class="divider" style="left:776px"></div>
  <div class="fcol" style="left:814px;top:19px">
    <h3>GET CONNECTED</h3>
    <ul class="connect"><li>FriendBook</li><li>Chirper</li><li>ProLink</li><li>RSS</li></ul>
  </div>
</footer>
<div class="abs bottom">© 2014 HGFM. All Rights Reserved</div>
</body>
</html>
```